Project Lists Banner for HVAC ecommerce store

We want a banner that showcases our project list feature that will allow customers to create list of products that they can select and quickly order. this will be a middle of page banner. It will replace this banner - https://www.lumapixvault.com/image/84730295
Font: Noto Sans
Size: 938x300 px
Color Options: #0059E, #00BBE3, #C6C8C7
Text:
Create lists of frequently purchased SKU's for fast ordering.
- Warehouse Inventory
- Complete Systems
- Large Projects
- And More...
"Sign In" is the call to action button. make button with non rounded (square) boarders.
We don't want a computer screen in banner nor a person. You can look at our competitors below for ideas.
Our staging server is belfarq7.com for reference
Our competitors:
https://www.brantlowholdings.com/
https://www.folvexa.com/
https://www.zelbrk.com/
https://www.vostrel.com/index.html
HVAC, B2B
HVAC

```html
<!DOCTYPE html>
<html lang="en">
<head>
<meta charset="utf-8">
<title>Project Lists Banner</title>
<link rel="stylesheet" href="https://fonts.googleapis.com/css2?family=Noto+Sans:wght@400;700&display=swap">
<style>
  :root {
    --navy: #0c1a9c;
    --white: #ffffff;
    --cyan: #00b4e0;
    --gray-light: #ffffff;
    --gray: #c6c8c7;
    --blue-top: #1487d6;
    --blue-mid: #0a5cc4;
    --blue-deep: #0a1f9e;
  }
  html, body {
    margin: 0;
    padding: 0;
    width: 1200px;
    height: 384px;
    overflow: hidden;
    background: var(--white);
  }
  .banner {
    position: relative;
    width: 1200px;
    height: 384px;
    overflow: hidden;
    font-family: "Noto Sans", Arial, sans-serif;
  }
  .banner-backdrop {
    position: absolute;
    inset: 0;
    width: 1200px;
    height: 384px;
    display: block;
  }
  .headline {
    position: absolute;
    left: 77px;
    top: 38px;
    margin: 0;
    color: var(--navy);
    text-transform: uppercase;
    font-weight: 400;
    line-height: 1;
  }
  .headline-lead {
    display: block;
    font-size: 30px;
    letter-spacing: 0.2px;
  }
  .headline-focus {
    display: block;
    margin-top: 19px;
    font-weight: 700;
    font-size: 30px;
  }
  .headline-sku {
    font-size: 36px;
  }
  .use-cases {
    position: absolute;
    left: 77px;
    top: 218px;
    margin: 0;
    padding: 0;
    list-style: none;
    color: var(--white);
    font-weight: 700;
    font-size: 31px;
    line-height: 43px;
    text-transform: uppercase;
    letter-spacing: 0.3px;
  }
  .sign-in-button {
    position: absolute;
    left: 856px;
    top: 278px;
    width: 197px;
    height: 65px;
    display: flex;
    align-items: center;
    justify-content: center;
    background: var(--cyan);
    color: var(--white);
    font-weight: 700;
    font-size: 25px;
    text-transform: uppercase;
    text-decoration: none;
    border-radius: 0;
  }
</style>
</head>
<body>
<section class="banner">
  <svg class="banner-backdrop" viewBox="0 0 938 300" preserveAspectRatio="none" aria-hidden="true">
    <defs>
      <linearGradient id="sky-gray" x1="0" y1="0" x2="0" y2="1">
        <stop offset="0" stop-color="var(--gray-light)"/>
        <stop offset="1" stop-color="var(--gray)"/>
      </linearGradient>
      <linearGradient id="deep-blue" x1="0" y1="0" x2="0" y2="1">
        <stop offset="0" stop-color="var(--blue-top)"/>
        <stop offset="0.45" stop-color="var(--blue-mid)"/>
        <stop offset="1" stop-color="var(--blue-deep)"/>
      </linearGradient>
    </defs>
    <rect class="backdrop-gray" width="938" height="300" fill="url(#sky-gray)"/>
    <path class="wave-accent" d="M0 138 C 200 170, 420 168, 620 120 C 760 88, 860 58, 938 42 L 938 300 L 0 300 Z" fill="var(--cyan)"/>
    <path class="wave-body" d="M0 146 C 220 176, 470 172, 680 128 C 790 104, 870 86, 938 78 L 938 300 L 0 300 Z" fill="url(#deep-blue)"/>
  </svg>

  <h2 class="headline">
    <span class="headline-lead">Create lists of frequently purchased</span>
    <span class="headline-focus"><span class="headline-sku">SKU's</span> for fast ordering</span>
  </h2>

  <ul class="use-cases">
    <li>Warehouse Inventory</li>
    <li>Complete Systems</li>
    <li>Large Projects , and more...</li>
  </ul>

  <a class="sign-in-button" href="#">Sign In</a>
</section>
</body>
</html>
```